Enrollment Campaign

We need a flyer design for our school's enrollment campaign. Our school website is www.tbvacademy.net.

The flyer should be double sided.

I want the reader to get the following messages:
1. Montessori graduates are leading the top companies of our time.
2. We are an accredited Montessori school.
3. Enrollment is open now for all four programs:
a) Toddler: 18months (or as soon as the child is able to walk) - 3 years
b) CASA: Preschool to Senior Kindergarten (3 years to 6 years)
c) Elementary: Grades 1 to 6
d) Junior High: Grades 7 to 8
4) Our contact information:
website, email:info@tbvacademy.net, phone: 647 382 5146
5) Call for Action: Book a Tour! (there is a button on our website to book a tour)
6) In the languages punjabi, hindi and italian, I wouldn't readers to know that we offer their faith and cultural education as well.
7) Fees for children under age of 6 can be claimed in Taxes as day care expense. So, there is no reason to miss providing our children the best that we can in education.
Updates

Please note my updates to my brief in the "must have" section. Also, I have added some pics that can be used. Please note that I don't have one pic (the farming one referred to in my brief). I will really appreciate if you can kindly update your design accordingly.

Reason: Because of my recent update to the brief, some designers need some time to adjust their designs. I really appreciate your patience and kind consideration for my project. Thank you!

Industry/Entity Type

Education

Colors

Designer to choose colors to be used in the design.

Requirements
Must have
• Must have a unique design. I don't want a typical flyer. The design should be unique and memorable.

One of the main pics that I need is for illustrating a key feature of our new Junior High program that we are starting in August 2015. The key feature is that children are going to be operating a 'greenhouse', growing organic produce and will also be preparing their daily lunch from scratch. So, show a pic of a 13-14year old farming or something.

```html
<!DOCTYPE html>
<html lang="en">
<head>
<meta charset="utf-8">
<title>TBV Academy – Enrollment Flyer</title>
<link rel="stylesheet" href="https://fonts.googleapis.com/css2?family=Ubuntu:wght@300;400;500;700&display=swap">
<style>
  :root {
    --backdrop: #e4e4e4;
    --paper: #f5f4f0;
    --olive: #5b6b2c;
    --olive-dark: #4a5822;
    --lime: #b8d430;
    --sky: #2b93cf;
    --ink: #555a3a;
    --bubble: #dcdec6;
    --white: #ffffff;
  }
  * { box-sizing: border-box; margin: 0; padding: 0; }
  html, body { width: 847px; height: 1200px; overflow: hidden; }
  body {
    background: var(--backdrop);
    font-family: "Ubuntu", Arial, sans-serif;
    position: relative;
  }
  .flyer {
    position: absolute;
    left: 248px;
    width: 330px;
    height: 429px;
    overflow: hidden;
    box-shadow: 0 4px 14px rgba(0,0,0,.18);
  }

  /* ---------- Front side ---------- */
  .front { top: 66px; }
  .front-photo {
    position: absolute; left: 0; top: 0; width: 270px; height: 429px;
    background: linear-gradient(180deg, #6f8f45 0%, #86a255 22%, #7a8f5a 42%, #4f74a8 62%, #3d68a8 82%, #4d6330 100%);
  }
  .natural-badge {
    position: absolute; left: 14px; top: 8px; width: 50px; height: 80px;
    background: var(--olive-dark);
    border-radius: 6px 6px 2px 2px;
  }
  .front-brand {
    position: absolute; left: 0; width: 270px; top: 398px;
    text-align: center; color: var(--white);
    font-size: 13px; font-weight: 500;
  }
  .front-band {
    position: absolute; left: 270px; top: 0; width: 60px; height: 429px;
    background: var(--olive);
  }
  .band-inner {
    position: absolute; left: 0; top: 429px;
    width: 429px; height: 60px;
    transform-origin: 0 0; transform: rotate(-90deg);
    display: flex; align-items: center;
    padding: 0 8px 0 4px;
    color: var(--white);
  }
  .program-title { width: 104px; line-height: 1.05; white-space: nowrap; }
  .program-title .new { color: var(--lime); font-size: 15px; font-weight: 300; }
  .program-title .name { font-size: 14px; font-weight: 700; letter-spacing: .3px; }
  .program-title .word { font-size: 13px; font-weight: 300; letter-spacing: 1px; }
  .program-detail {
    flex: 1; border-left: 1px solid var(--white);
    padding-left: 8px; margin-left: 2px; line-height: 1.15;
  }
  .program-detail .date { font-size: 13.5px; font-weight: 700; }
  .program-detail p { font-size: 9.5px; font-weight: 300; }
  .program-detail .hl { color: var(--lime); font-weight: 500; }

  /* ---------- Back side ---------- */
  .back { top: 671px; background: var(--paper); color: var(--ink); }
  .col-left { position: absolute; left: 34px; top: 26px; width: 118px; }
  .lead { color: var(--sky); font-size: 8.4px; font-weight: 700; line-height: 1.3; }
  .accredited { margin-top: 6px; font-size: 10px; color: var(--olive); line-height: 1.2; }
  .accredited strong { display: block; font-size: 9.6px; font-weight: 700; letter-spacing: .3px; }
  .photo-teacher {
    margin-top: 6px; width: 116px; height: 82px;
    background: linear-gradient(135deg, #b28c63 0%, #e2d6bf 45%, #c8a47a 75%, #8c6b48 100%);
  }
  .enroll {
    margin-top: 14px; padding: 5px 0 6px;
    border-top: 2px solid var(--olive); border-bottom: 2px solid var(--olive);
    font-size: 14px; font-weight: 700; line-height: 1.15; color: var(--olive);
    letter-spacing: .3px;
  }
  .programs { list-style: none; margin-top: 8px; font-size: 6px; line-height: 1.2; }
  .programs li { position: relative; padding-left: 9px; margin-bottom: 3px; }
  .programs li::before {
    content: ""; position: absolute; left: 0; top: 1.5px;
    width: 4px; height: 4px; background: var(--ink);
  }
  .programs b { font-size: 6.8px; font-weight: 700; }
  .back-brand {
    margin-top: 26px; margin-left: 16px;
    font-size: 14px; font-weight: 500; color: var(--sky);
  }
  .col-right { position: absolute; left: 175px; top: 0; width: 142px; }
  .photo-child {
    width: 142px; height: 160px;
    background: linear-gradient(160deg, #efe6d6 0%, #c9b08c 40%, #b5452f 62%, #8a6a45 85%, #5a4632 100%);
  }
  .culture { margin-top: 13px; font-size: 7.4px; line-height: 1.3; color: var(--olive); }
  .fees { margin-top: 8px; font-size: 7.2px; line-height: 1.3; color: var(--sky); }
  .cta {
    margin-top: 8px; width: 142px; height: 22px; padding: 3px 10px 0 6px;
    background: var(--olive); color: var(--white); line-height: 1.15;
    white-space: nowrap;
    clip-path: polygon(0 0, 100% 0, 94% 50%, 100% 100%, 0 100%);
  }
  .cta strong { display: block; font-size: 6.8px; font-weight: 700; }
  .cta span { display: block; font-size: 5.3px; }
  .contact { position: absolute; left: 178px; top: 302px; width: 130px; height: 124px; }
  .contact svg { position: absolute; left: 0; top: 0; }
  .contact-body { position: absolute; left: 16px; top: 10px; width: 112px; font-size: 7.3px; color: var(--ink); }
  .contact-body h3 {
    font-size: 10px; font-weight: 400; color: var(--olive);
    text-align: center; line-height: 1.05; margin-bottom: 6px;
  }
  .contact-body li { list-style: none; display: flex; gap: 4px; margin-bottom: 2px; line-height: 1.2; }
  .contact-body li svg { position: static; flex: none; margin-top: 1px; }
</style>
</head>
<body>

<section class="flyer front" aria-label="Flyer front">
  <div class="front-photo" role="img" aria-label="Photo of a smiling boy in a straw hat and blue organic t-shirt holding fresh plums in an orchard"></div>
  <div class="natural-badge" role="img" aria-label="Natural product badge"></div>
  <div class="front-brand">TBV Academy</div>
  <div class="front-band">
    <div class="band-inner">
      <div class="program-title">
        <div class="new">NEW</div>
        <div class="name">JUNIOR HIGH</div>
        <div class="word">PROGRAM</div>
      </div>
      <div class="program-detail">
        <div class="date">Starting in August 2015</div>
        <p>Children are going to be operating a <span class="hl">'greenhouse'</span>, growing <span class="hl">organic produce</span> and will also be preparing their <span class="hl">daily lunch</span> from scratch</p>
      </div>
    </div>
  </div>
</section>

<section class="flyer back" aria-label="Flyer back">
  <div class="col-left">
    <p class="lead">Montessori graduates are leading the top companies of our time</p>
    <p class="accredited">We are an accredited <strong>MONTESSORI SCHOOL</strong></p>
    <div class="photo-teacher" role="img" aria-label="Photo of a teacher working with a student at a classroom table"></div>
    <h2 class="enroll">ENROLLMENT<br>IS OPEN NOW<br>FOR ALL FOUR<br>PROGRAMS</h2>
    <ul class="programs">
      <li><b>Toddler</b><br>18months (or as soon as the child is able to walk) – 3 years</li>
      <li><b>CASA</b><br>Preschool to Senior Kindergarten (3 years to 6 years)</li>
      <li><b>Elementary</b> Grades 1 to 6</li>
      <li><b>Junior High</b> Grades 7 to 8</li>
    </ul>
    <div class="back-brand">TBV Academy</div>
  </div>

  <div class="col-right">
    <div class="photo-child" role="img" aria-label="Photo of a young child in a red vest doing a hands-on Montessori activity"></div>
    <p class="culture">In the languages punjabi, hindi and italian, I wouldn't readers to know that we offer their faith and cultural education as well.</p>
    <p class="fees">Fees for children under age of 6 can be claimed in Taxes as day care expense. So, there is no reason to miss providing our children the best that we can in education.</p>
    <div class="cta">
      <strong>Call for Action: Book a Tour !</strong>
      <span>there is a button on our website to book a tour</span>
    </div>
  </div>

  <div class="contact">
    <svg width="130" height="124" viewBox="0 0 130 124" aria-hidden="true">
      <circle cx="68" cy="58" r="56" fill="var(--bubble)"/>
      <path d="M28 90 L2 120 L50 108 Z" fill="var(--bubble)"/>
    </svg>
    <div class="contact-body">
      <h3>Our contact<br>information</h3>
      <ul>
        <li><svg width="7" height="7" viewBox="0 0 10 10"><circle cx="5" cy="5" r="4.2" fill="none" stroke="currentColor" stroke-width="1.4"/><path d="M1 5h8M5 1v8" stroke="currentColor" stroke-width="1"/></svg>www.tbvacademy.net</li>
        <li><svg width="7" height="7" viewBox="0 0 10 10"><rect x="0.5" y="2" width="9" height="6" fill="none" stroke="currentColor" stroke-width="1.2"/><path d="M0.5 2l4.5 3.5L9.5 2" fill="none" stroke="currentColor" stroke-width="1.2"/></svg>info@tbvacademy.net</li>
        <li><svg width="7" height="7" viewBox="0 0 10 10"><path d="M2 1l2 2-1 1.5a6 6 0 0 0 2.5 2.5L7 6l2 2-1.5 1.5C4 9 1 6 .5 2.5z" fill="currentColor"/></svg>647-382-5146</li>
        <li><svg width="7" height="7" viewBox="0 0 10 10"><path d="M5 1L1 5h1.2v4h2.3V6.5h1V9h2.3V5H9z" fill="currentColor"/></svg>3-2870 Maplewood Drive<br>Oakridge, ON, K4R1T9</li>
      </ul>
    </div>
  </div>
</section>

</body>
</html>
```